Creating a Label for the Wine "Kemora"

Kemora
As you know Kemora is an imagined place or state of things in which everything is perfect. This wine reflects that. It is a high value wine and it is perfect. The dimensions shoulb be between 9c x 11,5 cm and 12cm x 8 cm

```html
<!DOCTYPE html>
<html lang="en">
<head>
<meta charset="UTF-8">
<title>Kemora Red Wine Label</title>
<link rel="stylesheet" href="https://fonts.googleapis.com/css2?family=Barlow:wght@400;600&display=swap">
<style>
  :root {
    --backdrop: #1b1b1b;
    --label-paper: #f7f7f6;
    --ink: #1a1a1a;
  }
  html, body {
    margin: 0;
    padding: 0;
    width: 1200px;
    height: 3025px;
    overflow: hidden;
    background: var(--backdrop);
  }
  .canvas {
    position: relative;
    width: 1200px;
    height: 3025px;
  }
  .wine-label {
    position: absolute;
    left: 150px;
    top: 937px;
    width: 900px;
    height: 1150px;
    background: var(--label-paper);
    color: var(--ink);
    font-family: "Barlow", "Helvetica Neue", Arial, sans-serif;
  }
  .brand-mark {
    position: absolute;
    left: 50%;
    top: 228px;
    width: 130px;
    height: 130px;
    margin-left: -65px;
    border-radius: 50%;
    background: var(--ink);
  }
  .brand-name {
    position: absolute;
    left: 0;
    right: 0;
    top: 648px;
    margin: 0;
    text-align: center;
    font-weight: 600;
    font-size: 108px;
    line-height: 1;
    letter-spacing: 4px;
  }
  .wine-type {
    position: absolute;
    left: 0;
    right: 0;
    top: 940px;
    margin: 0;
    text-align: center;
    font-weight: 400;
    font-size: 44px;
    line-height: 1;
    letter-spacing: 12px;
  }
</style>
</head>
<body>
  <main class="canvas">
    <section class="wine-label">
      <div class="brand-mark"></div>
      <h1 class="brand-name">KEMORA</h1>
      <p class="wine-type">RED WINE</p>
    </section>
  </main>
</body>
</html>
```